Clinic for cellulit and fat removal

Name of clinic :
Lirava
- Body & Health (this has to be written on the site.)
I need CMS for me to be able to make changes myself.
A webpage for woman searching for a solution to remove fat and cellulit.
The owner is a brazilian woman in Denmark, and want her sense of aestetic shines thru the website.
There needs to be a slide show on the landing page showing big sliding pictures, of the clinic and and the treatments.
The Cryolipolysis, is a treatment freezing fat and cellulit, and this treatment will be the Attraction of the clinic.
Needs These pages in a horisontal fasion. (written in Danish)
Lirava
Behandlinger
- Cryolipolysis
- Trimflox
- Lymfemassage
- Korathelix
- Amberline Tide
Produkter
Priser
Kontakt
Clinic
Coded - Design and coding required
5+ page

```html
<!DOCTYPE html>
<html lang="da">
<head>
<meta charset="utf-8">
<title>Lirava – Body &amp; Health</title>
<link rel="stylesheet" href="https://fonts.googleapis.com/css2?family=Jost:wght@200;300;400;500&display=swap">
<style>
:root{
  --brown-deep:#5b3419;
  --brown-text:#6a4730;
  --brown-soft:#8a6a55;
  --body-text:#5c5149;
  --cream:#fdf4ee;
  --rule:#e7ddd5;
  --white:#ffffff;
  --btn-top:#f5e6da;
  --btn-bottom:#ecd6c5;
  --player:#2c2c2c;
  --progress:#3a78c2;
}
*{margin:0;padding:0;box-sizing:border-box}
html,body{width:1200px;height:2426px;overflow:hidden;background:var(--white)}
body{position:relative;font-family:"Jost",sans-serif;color:var(--body-text)}
.abs{position:absolute}

/* header */
.brand-badge{left:100px;top:13px;width:136px;height:136px;border-radius:50%;background:var(--brown-deep);
  display:flex;align-items:center;justify-content:center;color:var(--white);font-weight:300;font-size:25px;letter-spacing:1px}
.lang-select{left:852px;top:23px;width:249px;height:38px;border:1px solid #cfc8c2;display:flex;align-items:center;padding:0 14px;
  font-size:13px;font-weight:500;letter-spacing:.6px;color:#333}
.lang-select svg{margin-right:10px}
.lang-select .caret{margin-left:auto}
.main-nav{top:96px;left:0;width:1200px;height:22px}
.main-nav a{position:absolute;top:0;font-size:15px;letter-spacing:1px;color:#333;text-decoration:none;font-weight:400}

/* hero */
.hero{left:0;top:158px;width:1200px;height:537px;
  background:linear-gradient(90deg,#d7ab8d 0%,#e6c3ab 22%,#d9d4d0 40%,#cfc6bf 60%,#e9e6e3 80%,#f3f1ef 100%)}
.hero-title{left:0;top:320px;width:1200px;text-align:center;font-weight:200;font-size:98px;color:var(--white);letter-spacing:1px;line-height:1}
.slide-dots{top:638px;left:578px;display:flex;gap:8px}
.slide-dots span{width:10px;height:10px;border-radius:50%;background:var(--white)}
.slide-dots span.off{background:transparent;border:1px solid var(--white)}

/* headings */
.section-title{left:0;width:1200px;text-align:center;font-weight:300;color:var(--brown-text);font-size:36px;letter-spacing:.5px;line-height:1}
.rule{height:1px;background:var(--rule)}

/* treatments */
.treatment-photo{top:876px;width:317px;height:207px}
.treatment-name{top:1101px;width:317px;text-align:center;font-weight:300;font-size:22px;color:var(--brown-text);letter-spacing:.3px}

/* testimonials */
.testimonials{left:0;top:1193px;width:1200px;height:401px;background:var(--cream)}
.quote-mark{font-size:70px;color:#d9d1cb;font-weight:500;line-height:1}
.quote-text{left:217px;top:1314px;width:766px;text-align:center;font-size:13.5px;line-height:22px;color:var(--body-text)}
.avatar{left:553px;top:1387px;width:84px;height:84px;border-radius:50%;border:3px solid var(--white);
  background:radial-gradient(circle at 50% 45%,#f2d9c4 0%,#d9b592 60%,#c4dce8 100%);box-shadow:0 0 0 1px #e2d6cc}
.patient-name{left:0;top:1488px;width:1200px;text-align:center;font-size:14px;letter-spacing:.6px;color:#3b2a20}
.testimonial-dots{left:572px;top:1533px;display:flex;gap:6px}
.testimonial-dots span{width:10px;height:10px;border-radius:50%;background:var(--brown-deep)}
.testimonial-dots span.off{background:transparent;border:1.5px solid var(--brown-deep)}

/* video */
.video-copy{left:100px;width:520px;font-size:13px;line-height:25px;color:var(--body-text)}
.more-btn{left:99px;top:1937px;width:234px;height:47px;background:linear-gradient(var(--btn-top),var(--btn-bottom));
  display:flex;align-items:center;justify-content:center;gap:12px;font-size:17px;letter-spacing:1px;color:var(--brown-text)}
.video-frame{left:669px;top:1711px;width:435px;height:276px;background:var(--white);border:1px solid #ddd;box-shadow:0 1px 4px rgba(0,0,0,.15)}
.video-still{left:681px;top:1722px;width:414px;height:227px;
  background:linear-gradient(160deg,#fff5c9 0%,#e7c06a 30%,#9b7a3c 60%,#5c5a36 100%)}
.video-bar{left:681px;top:1949px;width:414px;height:33px;background:var(--player)}

/* footer */
.site-footer{left:0;top:2055px;width:1200px;height:371px;background:var(--cream)}
.footer-brand{left:100px;top:2126px;font-size:34px;font-weight:300;color:var(--brown-deep);letter-spacing:1px;display:flex;align-items:center;gap:10px}
.footer-brand i{display:block;width:14px;height:14px;border-radius:50%;background:var(--brown-deep)}
.footer-about{left:100px;top:2186px;width:292px;font-size:12px;line-height:17.5px;color:var(--body-text)}
.col-rule{top:2102px;width:1px;height:214px;background:var(--rule)}
.col-title{top:2105px;font-size:15px;letter-spacing:1.6px;color:#3b2a20}
.col-list{top:2152px;list-style:none;font-size:12px;letter-spacing:.6px;line-height:23px;color:var(--brown-soft)}
.social{top:2198px;display:flex;gap:6px}
.social span{width:34px;height:34px;border-radius:50%;background:var(--brown-soft)}
.copyright{left:100px;top:2373px;font-size:12.5px;color:var(--body-text)}
.code{left:1070px;top:2373px;width:31px;text-align:right;font-size:12.5px;color:var(--body-text)}
</style>
</head>
<body>

<header>
  <div class="abs brand-badge">LIRAVA</div>
  <div class="abs lang-select">
    <svg width="22" height="22" viewBox="0 0 22 22"><circle cx="11" cy="11" r="11" fill="#c8102e"/><rect x="6" y="0" width="3" height="22" fill="#fff"/><rect x="0" y="9.5" width="22" height="3" fill="#fff"/></svg>
    DANISH
    <svg class="caret" width="10" height="6" viewBox="0 0 10 6"><path d="M1 1l4 4 4-4" stroke="#555" fill="none" stroke-width="1.3"/></svg>
  </div>
  <nav class="abs main-nav">
    <a style="left:469px">LIRAVA</a>
    <a style="left:585px">BEHANDLINGER <svg width="9" height="6" viewBox="0 0 9 6"><path d="M1 1l3.5 3.5L8 1" stroke="#333" fill="none" stroke-width="1.4"/></svg></a>
    <a style="left:776px">PRODUKTER</a>
    <a style="left:922px">PRISER</a>
    <a style="left:1028px">KONTAKT</a>
  </nav>
</header>

<section>
  <div class="abs hero" role="img" aria-label="Slideshow photo: a woman lying on a treatment bed receiving a body-contouring treatment"></div>
  <h1 class="abs hero-title">Body &amp; Health</h1>
  <div class="abs slide-dots"><span></span><span class="off"></span><span></span></div>
</section>

<section>
  <h2 class="abs section-title" style="top:766px">WE ARE A CELLULIT AND FAT REMOVAL CLINIC</h2>
  <div class="abs rule" style="left:99px;top:831px;width:1002px"></div>

  <div class="abs treatment-photo" style="left:99px;background:linear-gradient(135deg,#e9e4df,#b9c7cf 50%,#e6c8b2)" role="img" aria-label="Photo: suction cups of a cryolipolysis device on a leg"></div>
  <div class="abs treatment-photo" style="left:442px;background:linear-gradient(135deg,#d8d3cf,#efe7e0 50%,#c9b4a4)" role="img" aria-label="Photo: a handheld treatment device used on the skin"></div>
  <div class="abs treatment-photo" style="left:784px;background:linear-gradient(135deg,#f0ebe6,#d8a98a 50%,#5f9a94)" role="img" aria-label="Photo: hands giving a leg massage"></div>

  <h3 class="abs treatment-name" style="left:99px">MINIMA VENIAM</h3>
  <h3 class="abs treatment-name" style="left:442px">NOSTRUM EXERCITATION</h3>
  <h3 class="abs treatment-name" style="left:784px">ACCUSANTIUM DOLORE</h3>
</section>

<section>
  <div class="abs testimonials"></div>
  <h2 class="abs section-title" style="top:1239px">PATIENT TESTIMONIALS</h2>
  <div class="abs rule" style="left:527px;top:1289px;width:146px;background:#e3d3c6"></div>
  <div class="abs quote-mark" style="left:172px;top:1306px">&ldquo;</div>
  <p class="abs quote-text">But I must explain to you how all this mistaken idea of denouncing pleasure and praising pain was born and I will give you a complete account of the system, and expound the actual teachings of the great explorer of the truth, the master-builder of human happiness. No one rejects, dislikes, or avoids pleasure itself, because it is pleasure, but because those who do not know how to pursue pleasure.</p>
  <div class="abs quote-mark" style="left:985px;top:1355px">&rdquo;</div>
  <div class="abs avatar" role="img" aria-label="Portrait photo of the patient"></div>
  <div class="abs patient-name">ARCHITECTO BEATAE - CITY NAME</div>
  <div class="abs testimonial-dots"><span class="off"></span><span></span><span></span></div>
</section>

<section>
  <h2 class="abs section-title" style="top:1637px">OUR VIDEO</h2>
  <div class="abs rule" style="left:527px;top:1685px;width:146px"></div>
  <p class="abs video-copy" style="top:1720px">Sed ut perspiciatis unde omnis iste natus error sit voluptatem accusantium doloremque laudantium, totam rem aperiam, eaque ipsa quae ab illo inventore veritatis et quasi architecto beatae vitae dicta sunt explicabo.</p>
  <p class="abs video-copy" style="top:1823px">Nemo enim ipsam voluptatem quia voluptas sit aspernatur aut odit aut fugit, sed quia consequuntur magni dolores eos qui ratione voluptatem sequi nesciunt. Neque porro quisquam est, qui dolorem ipsum quia dolor sit amet.</p>
  <div class="abs more-btn">MORE INFORMATION <svg width="8" height="12" viewBox="0 0 8 12"><path d="M1.5 1.5L6 6l-4.5 4.5" stroke="#6a4730" fill="none" stroke-width="1.6"/></svg></div>

  <div class="abs video-frame"></div>
  <div class="abs video-still" role="img" aria-label="Video still: two people jogging on a sunlit tree-lined path"></div>
  <svg class="abs" style="left:851px;top:1801px" width="74" height="74" viewBox="0 0 74 74"><circle cx="37" cy="37" r="34" fill="none" stroke="#fff" stroke-width="3"/><path d="M29 22v30l24-15z" fill="#fff"/></svg>
  <div class="abs video-bar"></div>
  <svg class="abs" style="left:681px;top:1949px" width="414" height="33" viewBox="0 0 414 33">
    <path d="M11 10v13l11-6.5z" fill="#fff"/>
    <rect x="33" y="14" width="300" height="5" rx="2.5" fill="#ddd"/>
    <rect x="33" y="14" width="112" height="5" rx="2.5" fill="var(--progress)"/>
    <path d="M381 13h4l5-4v15l-5-4h-4z" fill="#fff"/>
    <path d="M393 12.5q3 4 0 8" stroke="#fff" fill="none" stroke-width="1.4"/>
  </svg>
</section>

<footer>
  <div class="abs site-footer"></div>
  <div class="abs footer-brand"><i></i>LIRAVA</div>
  <p class="abs footer-about">But I must explain to you how all this mistaken idea of denouncing pleasure and praising pain was born and I will give you a complete account of the system, and expound the actual teachings of the great explorer of the truth, the master-builder of human happiness</p>

  <div class="abs col-rule" style="left:427px"></div>
  <div class="abs col-rule" style="left:653px"></div>
  <div class="abs col-rule" style="left:881px"></div>

  <h4 class="abs col-title" style="left:474px">INFORMATION</h4>
  <ul class="abs col-list" style="left:474px">
    <li>LIRAVA</li><li>BEHANDLINGER</li><li>PRODUKTER</li><li>PRISER</li><li>KONTAKT</li>
  </ul>

  <h4 class="abs col-title" style="left:703px">MY ACCOUNT</h4>
  <ul class="abs col-list" style="left:703px">
    <li>MY ORDERS</li><li>MY CREDIT SLIPS</li><li>MY ADDRESSES</li><li>MY PERSONAL INFO</li><li>OUR LOCATION</li><li>VIEW MAP</li>
  </ul>

  <h4 class="abs col-title" style="left:931px">FOLLOW US</h4>
  <div class="abs col-list" style="left:931px">PLEASE CONNECT WITH US</div>
  <div class="abs social" style="left:931px" aria-label="Social media links"><span></span><span></span><span></span><span></span></div>

  <div class="abs rule" style="left:99px;top:2350px;width:1002px"></div>
  <div class="abs copyright">© 2017 Lirava.&nbsp; All right reserved&nbsp; Term of Use</div>
  <div class="abs code">C16</div>
</footer>

</body>
</html>
```